creation of a business card design for a company specializing in the creation...

I would like to create a design for a professional business card on a black background and with the company's colors (I am attaching some files: including the logo in horizontal and centered format, I am also attaching a recent project design a T-shirt, this is the one I chose to give you an idea of my preferences.

we are in the process of developing a new website design, it is still in the development phase but it can be viewed at the following address: www.vantrelmo.be to give you other ideas about the company
you will see for yourself the subject of my main activity: company specializing in the construction of stairs

I would like a business card that stands out from the rest with a unique design

here is the informations
Name: Lucien Barthel
Function: Manager
Address: Rue Moulinet du Parc 42
7180 La Louvière
telephone: +32 468 219 804
email: info@rx7p.be
website: rx7p. be
social networks: Facebook, YouTube, TikTok, Instagram

Target Market(s)

customer who wants to have a beautiful staircase built

Industry/Entity Type

contruction d'escalier

Contact Information for Business Card

Adresse. Numero de telephone, site web, le texte : "Createur d'escalier", logo recto-verso, icone des reseaux sociaux

Requirements
Must have
• the mention: Stair creator
Nice to have
• an illustration of a designer staircase
Should not have
• do not distort the logo

```html
<!DOCTYPE html>
<html lang="en">
<head>
<meta charset="utf-8">
<title>RX7P Business Card</title>
<link href="https://fonts.googleapis.com/css2?family=Montserrat:wght@400;500;600&display=swap" rel="stylesheet">
<style>
  :root {
    --backdrop: #1c1d21;
    --card-top: #175395;
    --card-bottom: #1c3a66;
    --brand-light: #7fb4e6;
    --brand-dark: #1f3c78;
    --text-light: #a9cdf0;
    --rule: #5d93cc;
  }
  * { margin: 0; padding: 0; box-sizing: border-box; }
  html, body {
    width: 1200px; height: 900px; overflow: hidden;
    background: var(--backdrop);
    font-family: "Montserrat", sans-serif;
  }
  .stage {
    width: 1200px; height: 900px;
    display: flex; align-items: center; justify-content: center; gap: 40px;
  }
  .card {
    position: relative;
    width: 540px; height: 310px;
    border-radius: 22px;
    background: linear-gradient(160deg, var(--card-top) 0%, var(--card-bottom) 100%);
    box-shadow: 0 20px 40px rgba(0,0,0,.45);
    overflow: hidden;
  }
  .brand {
    position: absolute;
    display: flex; align-items: center; gap: 14px;
  }
  .brand-mark {
    width: 34px; height: 34px;
    background: var(--brand-dark);
  }
  .brand-text { display: flex; flex-direction: column; }
  .brand-name {
    font-weight: 500;
    font-size: 46px;
    letter-spacing: 3px;
    color: var(--brand-light);
    line-height: 1;
  }
  .brand-tagline {
    margin-top: 4px;
    font-weight: 500;
    font-size: 8px;
    letter-spacing: 3.2px;
    text-transform: uppercase;
    color: var(--brand-light);
  }
  .card-front .brand {
    left: 50%; top: 50%;
    transform: translate(-50%, -50%);
  }
  .card-back .brand { left: 44px; bottom: 56px; }
  .card-back .brand-name { font-size: 38px; }
  .card-back .brand-tagline { font-size: 7px; letter-spacing: 2.6px; }
  .card-back .brand-mark { width: 28px; height: 28px; }
  .divider {
    position: absolute;
    left: 300px; top: 52px;
    width: 1px; height: 206px;
    background: var(--rule);
  }
  .contact {
    position: absolute;
    left: 326px; top: 48px;
    color: var(--text-light);
  }
  .contact-name { font-weight: 600; font-size: 20px; }
  .contact-role { font-size: 12px; margin-top: 2px; }
  .contact-address { font-size: 12px; margin-top: 14px; line-height: 1.35; }
  .contact-lines { list-style: none; margin-top: 14px; font-size: 12px; }
  .contact-lines li { display: flex; align-items: center; gap: 9px; line-height: 1.7; }
  .contact-lines svg { width: 12px; height: 12px; flex: none; }
  .social { display: flex; gap: 9px; margin-top: 12px; }
  .social span {
    width: 14px; height: 14px; border-radius: 3px;
    background: var(--text-light); opacity: .85;
  }
</style>
</head>
<body>
<main class="stage">
  <section class="card card-front">
    <div class="brand">
      <span class="brand-mark"></span>
      <div class="brand-text">
        <span class="brand-name">RX7P</span>
        <span class="brand-tagline">Original Staircases</span>
      </div>
    </div>
  </section>

  <section class="card card-back">
    <div class="brand">
      <span class="brand-mark"></span>
      <div class="brand-text">
        <span class="brand-name">RX7P</span>
        <span class="brand-tagline">Original Staircases</span>
      </div>
    </div>
    <span class="divider"></span>
    <div class="contact">
      <p class="contact-name">Lucien Barthel</p>
      <p class="contact-role">Manager</p>
      <p class="contact-address">Rue Moulinet du Parc 42<br>7180 La Louvière</p>
      <ul class="contact-lines">
        <li>
          <svg viewBox="0 0 12 12" fill="none" stroke="currentColor" stroke-width="1.3"><path d="M2.5 1.5l2 .3.6 2.2-1.2.9a6 6 0 0 0 3.2 3.2l.9-1.2 2.2.6.3 2A8.5 8.5 0 0 1 2.5 1.5z"/></svg>
          +32 468 219 804
        </li>
        <li>
          <svg viewBox="0 0 12 12" fill="none" stroke="currentColor" stroke-width="1.2"><rect x="1" y="2.5" width="10" height="7" rx="1"/><path d="M1.3 3l4.7 3.6L10.7 3"/></svg>
          info@rx7p.be
        </li>
        <li>
          <svg viewBox="0 0 12 12" fill="none" stroke="currentColor" stroke-width="1.1"><circle cx="6" cy="6" r="4.8"/><ellipse cx="6" cy="6" rx="2" ry="4.8"/><path d="M1.2 6h9.6"/></svg>
          www.rx7p.be
        </li>
      </ul>
      <div class="social" aria-label="Social network links">
        <span></span><span></span><span></span><span></span>
      </div>
    </div>
  </section>
</main>
</body>
</html>
```